Counseling Practice Business Card

I need a professional looking business card incorporating my new logo that was just completed. Card needs to incorporate my name and title, description of my specialty, my address, my phone number, my fax number, my email and my website URL. I need to be able to choose design on/with different paper colors and textures.
I do not have a lot of business card ideas so I am open to anything but I want bold,sharp, clear card without additional designs other than my logo (see attached file info). I am open to different color backgrounds or paper colors including black. I do not like traditional brackets around area codes in phone number or dashes between numbers in phone number. Am open to other ways of presenting including periods between numbers as appropriate. I do not know enough to know what I like yet but I want card to coordinate and work together with my logo. My practice emphasizes natural mental health interventions so any use of color (with background paper color or the blue and green in my logo) that elicits nature is nice. In addition to black, any natural brown or wood looking background might be desirable also. Most of the offerings so far look very similar and boring.

Target Market(s)

Potential therapy clients and other professionals

Contact Information for Business Card

Card information:
Gerald M. Whitcombe, Ph.D.
Licensed Clinical Psychologist
Integrative Health Coach
4812 Marlowe Ridge Blvd SE
Suite 310
Duluth, GA 30096
(770) 415-2983 phone
(770) 581-4096 fax
drgeraldwhitcombe@quillmarsh.net
brightfernwellness.net

Font styles to use
Serif
Sans Serif
Other font styles liked:
• anything that you think looks crisp, clear and easily readable

Requirements
Must have
• Any color used should coordinate with my logo design (see attached files).
• Card should be printed horizontally so top and bottom are longest sides of rectangle.
• Background color or paper color should complement and highlight logo. Do not like a white background. black, grey, brown or any color my logo would blend well with.
Nice to have
• I would like designer to utilize color to highlight letters/name or phone-fax-web symbols.
• Bottom edge of card could be highlighted if appropriate to an idea.
Should not have
• I would NOT want the card to have a pure white background at all.
• No clear cards.
• Cards should be oriented with long sides on bottom and top, NOT sides. DO NOT LIKE THIS THIN TALL ORIENTATION.

```html
<!DOCTYPE html>
<html lang="en">
<head>
<meta charset="utf-8">
<title>Brightfern Wellness – Business Card</title>
<link href="https://fonts.googleapis.com/css2?family=Roboto:wght@400;500;700&display=swap" rel="stylesheet">
<style>
  :root {
    --backdrop: #d3d4d3;
    --card-stone: #e4e6e1;
    --brand-blue: #2870b4;
    --brand-green: #116a3e;
    --grad-green: #0c6b47;
    --grad-blue: #2a6fae;
    --ink: #2e3133;
    --ink-soft: #43474a;
    --on-dark: #ffffff;
  }
  * { box-sizing: border-box; margin: 0; padding: 0; }
  html, body {
    width: 1200px; height: 852px; overflow: hidden;
    background: var(--backdrop);
    font-family: "Roboto", Arial, sans-serif;
  }
  .stage {
    width: 1200px; height: 852px;
    display: flex; align-items: center; justify-content: center; gap: 60px;
  }
  .card {
    position: relative;
    width: 520px; height: 300px;
    border-radius: 22px;
    overflow: hidden;
    box-shadow: 0 6px 14px rgba(0,0,0,0.18);
  }
  /* Front */
  .card--front {
    background: linear-gradient(35deg, var(--grad-green) 0%, #12685c 50%, var(--grad-blue) 100%);
    display: flex; align-items: center; justify-content: center;
  }
  .brand {
    display: flex; align-items: center; gap: 10px;
    font-weight: 500; letter-spacing: 0.3px; white-space: nowrap;
  }
  .brand__dot { border-radius: 50%; flex: none; }
  .card--front .brand { color: var(--on-dark); font-size: 40px; gap: 12px; }
  .card--front .brand__dot { width: 22px; height: 22px; background: var(--on-dark); }

  /* Back */
  .card--back { background: var(--card-stone); }
  .card--back .brand {
    position: absolute; left: 34px; top: 96px;
    color: var(--brand-blue); font-size: 22px;
  }
  .card--back .brand__dot { width: 14px; height: 14px; background: var(--brand-blue); }
  .holder { position: absolute; left: 36px; top: 200px; }
  .holder__name { color: var(--brand-blue); font-weight: 700; font-size: 17px; white-space: nowrap; }
  .holder__title { color: var(--ink); font-size: 10.5px; line-height: 1.4; margin-top: 3px; }
  .contact {
    position: absolute; left: 292px; top: 52px;
    color: var(--ink-soft); font-size: 10.5px; line-height: 1.35; white-space: nowrap;
  }
  .contact__address { margin-bottom: 8px; }
  .contact__row { display: flex; align-items: center; gap: 8px; height: 17px; }
  .contact__icon { width: 11px; height: 11px; fill: var(--brand-blue); flex: none; }
  .edge { position: absolute; left: 0; bottom: 0; }
  .website {
    position: absolute; right: 28px; bottom: 30px;
    color: var(--on-dark); font-size: 12px;
  }
</style>
</head>
<body>
<main class="stage">
  <section class="card card--front" aria-label="Card front">
    <div class="brand"><span class="brand__dot"></span>Brightfern Wellness</div>
  </section>

  <section class="card card--back" aria-label="Card back">
    <div class="brand"><span class="brand__dot"></span>Brightfern Wellness</div>

    <div class="holder">
      <div class="holder__name">Gerald M. Whitcombe, Ph.D.</div>
      <div class="holder__title">Licensed Clinical Psychologist<br>Integrative Health Coach</div>
    </div>

    <div class="contact">
      <div class="contact__address">4812 Marlowe Ridge Blvd SE<br>Suite 310<br>Duluth, GA 30096</div>
      <div class="contact__row">
        <svg class="contact__icon" viewBox="0 0 12 12" aria-hidden="true"><path d="M2.5 1 4.3 1 5 3.6 3.8 4.6C4.5 6 5.9 7.5 7.4 8.2L8.4 7 11 7.7 11 9.5C11 10.3 10.3 11 9.5 11 4.8 11 1 7.2 1 2.5 1 1.7 1.7 1 2.5 1Z"/></svg>
        <span>770.415.2983</span>
      </div>
      <div class="contact__row">
        <svg class="contact__icon" viewBox="0 0 12 12" aria-hidden="true"><rect x="3" y="1" width="6" height="3"/><rect x="1" y="4.5" width="10" height="4.5" rx="1"/><rect x="3" y="8" width="6" height="3"/></svg>
        <span>770.581.4096</span>
      </div>
      <div class="contact__row">
        <svg class="contact__icon" viewBox="0 0 12 12" aria-hidden="true"><path d="M1 2.5h10v7H1z M1 2.5 6 6.5 11 2.5" stroke="#e4e6e1" stroke-width="0.9"/></svg>
        <span>drgeraldwhitcombe@quillmarsh.net</span>
      </div>
    </div>

    <svg class="edge" width="520" height="300" viewBox="0 0 520 300" aria-hidden="true">
      <rect x="0" y="286" width="340" height="14" fill="var(--brand-green)"/>
      <path d="M306 300 L318 236 Q320 226 332 226 L520 226 L520 300 Z" fill="var(--brand-blue)"/>
    </svg>
    <div class="website">brightfernwellness.net</div>
  </section>
</main>
</body>
</html>
```